Current state of Man's Soul Christian view

I would like an improvement of my design or a reimagining of my design to help people visualize what happens to the soul after we die. The second picture "screenshot 2023" is not my design but gives another idea.

For further information, there are 4 "time" frames that could be sectioned off. Eden is one time. Then adam rebellion and pre messiah earth (with hades/ Sheol). The third time frame is Jesus death, resurrection with the current state of earth. The 4th time frame is the "heavenly realm" which is across all 3 times and is unchanged.

For color ideas, please see my website www.lanternfieldnotes.org which has my color theme. But the death of Jesus I would like in some type of red as well as the death of believers.

My goal is something simple, engaging, and easy to understand. If you have any questions please lmk.
Thank you for considering my project.

```html
<!DOCTYPE html>
<html lang="en">
<head>
<meta charset="utf-8">
<title>Current State of Man's Soul</title>
<link rel="stylesheet" href="https://fonts.googleapis.com/css2?family=Oswald:wght@600&family=Inter:wght@500;600&display=swap">
<style>
  :root {
    --bg: #1c1c20;
    --gold: #d98c1f;
    --arrow: #e9a82c;
    --red: #e51d2a;
    --white: #ffffff;
    --frame: #8d8d92;
    --navy: #13294b;
    --ink: #1b1b1f;
    --eden-tint: rgba(233,168,44,0.07);
    --era-tint: rgba(255,255,255,0.025);
  }
  * { margin: 0; padding: 0; box-sizing: border-box; }
  html, body { width: 1200px; height: 849px; overflow: hidden; background: var(--bg); }
  .canvas {
    position: relative; width: 1200px; height: 849px; overflow: hidden;
    font-family: "Inter", Arial, sans-serif; color: var(--white);
  }
  .backdrop {
    position: absolute; inset: 0;
    background:
      radial-gradient(ellipse 40% 30% at 60% 52%, #3a3a44 0%, transparent 70%),
      linear-gradient(180deg, #222227 0%, #26262d 55%, #1d1d22 100%);
  }
  .rule { position: absolute; height: 1.5px; background: var(--gold); }
  .title {
    position: absolute; left: 108px; top: 34px;
    font-family: "Oswald", Impact, sans-serif; font-weight: 600;
    font-size: 62px; line-height: 80px; letter-spacing: 0.5px;
    color: var(--gold); white-space: nowrap;
  }
  .falling-figure {
    position: absolute; left: 12px; top: 26px; width: 78px; height: 206px;
    background: linear-gradient(180deg, rgba(217,140,31,0.15) 0%, rgba(217,140,31,0.75) 45%, var(--gold) 100%);
    clip-path: polygon(40% 0, 60% 0, 58% 45%, 90% 60%, 70% 100%, 45% 100%, 20% 60%, 0 52%, 42% 45%);
  }
  .era-frame {
    position: absolute; left: 39px; top: 233px; width: 544px; height: 563px;
    border: 1.5px solid var(--frame); border-radius: 20px; background: var(--era-tint);
  }
  .eden-zone {
    position: absolute; left: 40.5px; top: 234.5px; width: 72px; height: 560px;
    border-radius: 19px 0 0 19px; background: var(--eden-tint);
    border-right: 1px dashed rgba(233,168,44,0.35);
  }
  .current-era-frame {
    position: absolute; left: 596px; top: 245px; width: 592px; height: 551px;
    border: 1.5px solid var(--frame); border-radius: 20px; background: var(--era-tint);
  }
  .heaven-realm {
    position: absolute; left: 596px; top: 134px; width: 592px; height: 105px;
    border: 1.5px dashed rgba(240,192,96,0.55); border-radius: 14px;
  }
  .timeline { position: absolute; left: 112px; top: 268px; width: 4px; height: 438px; background: var(--red); border-radius: 2px; }
  .eden-label {
    position: absolute; left: 40px; top: 470px; width: 56px; text-align: center;
    font-size: 27px; font-weight: 500; transform: rotate(-90deg); transform-origin: center;
  }
  .death-badge {
    position: absolute; background: var(--red); color: var(--white);
    font-weight: 600; font-size: 21px; line-height: 28px; text-align: center; border-radius: 2px;
  }
  .jesus-death {
    position: absolute; left: 492px; top: 400px; width: 86px; height: 56px;
    background: var(--red); border-radius: 2px; text-align: center;
    font-weight: 600; font-size: 21px; line-height: 25px; padding-top: 3px;
  }
  .label { position: absolute; font-weight: 600; line-height: 1.12; }
  .label-lg { font-size: 22px; }
  .label-sm { font-size: 16px; }
  .centered { text-align: center; }
  .right { text-align: right; }
  .globe { position: absolute; border-radius: 50%; overflow: hidden; border: 1.5px solid #d8d8d8; }
  .globe-fallen { background: radial-gradient(circle at 45% 40%, #2f5d66 0%, #3d3a33 45%, #a54a14 80%, #2a1d16 100%); }
  .globe-current { background: radial-gradient(circle at 40% 35%, #e9f1f8 0%, #3d7cc0 35%, #1d4f97 70%, #0f2d63 100%); }
  .globe-band { position: absolute; left: 0; right: 0; bottom: 0; height: 75px; background: rgba(214,224,236,0.92); }
  .hades { position: absolute; width: 224px; height: 224px; border-radius: 50%; overflow: hidden; border: 1.5px solid #d8d8d8; }
  .hades-paradise { position: absolute; left: 0; top: 0; width: 100%; height: 50%;
    background: linear-gradient(180deg, #c39a3a 0%, #f4dc8a 55%, #e3b54b 100%); }
  .hades-torment { position: absolute; left: 0; bottom: 0; width: 100%; height: 50%;
    background: radial-gradient(ellipse at 50% 80%, #ff5a1a 0%, #b0230f 45%, #3a0c0a 100%); }
  .hades-divider { position: absolute; left: 0; right: 0; top: 50%; height: 2px; background: #f0a429; }
  .hades-name { position: absolute; left: 0; right: 0; text-align: center; font-weight: 600; font-size: 22px; }
  .hades-name.on-light { color: var(--ink); top: 18px; }
  .hades-name.on-dark { top: 124px; }
  .heaven-box {
    position: absolute; left: 605px; top: 142px; width: 414px; height: 89px;
    border-radius: 9px; border: 1.5px solid #f0c060;
    background: linear-gradient(180deg, #e4ecf1 0%, #f5f5f0 60%, #ece9df 100%);
    color: var(--ink); text-align: center; font-weight: 600; font-size: 27px; line-height: 34px; padding-top: 12px;
  }
  .resurrection-box {
    position: absolute; left: 601px; top: 474px; width: 152px; height: 62px;
    background: var(--white); border-radius: 7px; color: var(--navy);
    text-align: center; font-weight: 600; font-size: 21px; line-height: 22px; padding-top: 9px;
  }
  .arrows { position: absolute; inset: 0; }
</style>
</head>
<body>
<div class="canvas">
  <div class="backdrop" role="img" aria-label="Dark night landscape with trees, lake and hills"></div>

  <div class="rule" style="left:0; top:23px; width:825px;"></div>
  <div class="rule" style="left:52px; top:123px; width:773px;"></div>
  <div class="falling-figure" role="img" aria-label="Golden silhouette of a man falling from a beam of light"></div>
  <h1 class="title">CURRENT STATE OF MAN'S SOUL</h1>

  <!-- Time frame sections -->
  <div class="heaven-realm"></div>
  <div class="era-frame"></div>
  <div class="eden-zone"></div>
  <div class="current-era-frame"></div>

  <!-- Eden and old covenant era -->
  <div class="timeline"></div>
  <div class="eden-label">Eden</div>
  <div class="death-badge" style="left:118px; top:468px; width:90px;">DEATH</div>
  <div class="label label-lg" style="left:129px; top:406px;">Adam<br>Rebellion</div>

  <div class="globe globe-fallen" role="img" aria-label="Burning, ruined Earth before the Messiah" style="left:243px; top:250px; width:222px; height:222px;"></div>
  <div class="label label-lg centered" style="left:248px; top:395px; width:200px;">Pre-Messiah<br>Fallen Earth</div>

  <div class="jesus-death">JESUS<br>DEATH</div>

  <div class="label label-sm" style="left:129px; top:564px;">Narrow Gate</div>
  <div class="label label-sm" style="left:129px; top:655px;">Wide Gate</div>

  <div class="hades" role="img" aria-label="Hades split into a golden paradise gate above and fiery torment below" style="left:253px; top:517px;">
    <div class="hades-paradise"></div>
    <div class="hades-torment"></div>
    <div class="hades-divider"></div>
    <div class="hades-name on-light">Paradise</div>
    <div class="hades-name on-dark">Torment</div>
  </div>
  <div class="label label-lg centered" style="left:265px; top:750px; width:200px;">Hades/Sheol</div>

  <!-- Heavenly realm -->
  <div class="heaven-box" role="img" aria-label="Bright clouds of heaven">3rd Heaven<br>- God’s Heavenly Throne</div>

  <!-- Current era -->
  <div class="label label-lg" style="left:735px; top:299px;">Holy<br>Spirit<br>Descends</div>

  <div class="globe globe-current" role="img" aria-label="Blue Earth with clouds, as seen today" style="left:852px; top:252px; width:222px; height:222px;">
    <div class="globe-band"></div>
  </div>
  <div class="label label-lg centered" style="left:863px; top:405px; width:200px; color:var(--ink);">Current<br>Fallen Earth</div>

  <div class="death-badge" style="left:1082px; top:377px; width:94px;">DEATH</div>
  <div class="label label-lg right" style="left:1000px; top:212px; width:137px;">Believers<br>in Jesus</div>
  <div class="label label-lg right" style="left:1000px; top:490px; width:145px;">Non<br>-Believers</div>

  <div class="hades" role="img" aria-label="Hades split into a golden paradise gate above and fiery torment below" style="left:854px; top:517px;">
    <div class="hades-paradise"></div>
    <div class="hades-torment"></div>
    <div class="hades-divider"></div>
    <div class="hades-name on-light">Paradise</div>
    <div class="hades-name on-dark">Torment</div>
  </div>
  <div class="label label-lg centered" style="left:866px; top:750px; width:200px;">Hades/Sheol</div>

  <div class="resurrection-box">Jesus<br>Resurrection</div>

  <svg class="arrows" width="1200" height="849" viewBox="0 0 1200 849" aria-hidden="true">
    <g fill="none" stroke="#8d8d92" stroke-width="1.5">
      <path d="M488 262 V400 M488 456 V551 Q488 557 482 557 H430"/>
      <line x1="118" y1="590" x2="259" y2="590"/>
      <line x1="118" y1="630" x2="583" y2="630"/>
      <line x1="118" y1="702" x2="277" y2="702"/>
    </g>
    <g fill="none" stroke="#e9a82c" stroke-width="4.5" stroke-linecap="round" stroke-linejoin="round">
      <polyline points="88,476 94,483 88,490"/><polyline points="95,476 101,483 95,490"/>
      <polyline points="235,568 242,575 235,582"/><polyline points="242,568 249,575 242,582"/>
      <polyline points="221,658 228,665 221,672"/><polyline points="228,658 235,665 228,672"/>
      <polyline points="525,479 534,487 543,479"/><polyline points="525,487 534,495 543,487"/>
      <polyline points="524,580 516,589 524,598"/><polyline points="532,580 524,589 532,598"/>
      <line x1="675" y1="789" x2="675" y2="542"/>
      <line x1="675" y1="469" x2="675" y2="262"/>
      <path d="M720 260 V390 Q720 400 730 400 H830"/>
      <path d="M1082 365 H1146 Q1155 365 1155 356 V195 Q1155 186 1146 186 H1045"/>
      <path d="M1082 416 H1150 Q1159 416 1159 425 V620 Q1159 629 1150 629 H1096"/>
    </g>
    <g fill="#e9a82c">
      <polygon points="675,255 663,284 675,277 687,284"/>
      <polygon points="836,400 804,388 812,400 804,412"/>
      <polygon points="1040,186 1069,173 1062,186 1069,199"/>
      <polygon points="1091,629 1120,616 1113,629 1120,642"/>
    </g>
  </svg>
</div>
</body>
</html>
```